Business Card Design (NEW FILES)

ATTENTION: New vector files are available. Please update your design to reflect/use the new (better resolution) logo images.

Seeking a unique and professional business card design for a commercial drone photography/videography business. The layout should feature
the logo (attached) and include the following information:
Owen Tarrick
614-502-7738
www.skylarkreelworks.example
NRD Certified Remote Pilot

Owen Tarrick

```html
<!DOCTYPE html>
<html lang="en">
<head>
<meta charset="utf-8">
<title>Skylark Reelworks Business Card</title>
<link href="https://fonts.googleapis.com/css2?family=Open+Sans:wght@400;600;700;800&display=swap" rel="stylesheet">
<style>
  :root {
    --backdrop: #222222;
    --navy: #161a47;
    --orange: #e58650;
    --orange-deep: #c96f3d;
    --white: #ffffff;
  }
  * { margin: 0; padding: 0; box-sizing: border-box; }
  html, body { width: 1200px; height: 780px; overflow: hidden; }
  body {
    background: var(--backdrop);
    font-family: "Open Sans", sans-serif;
    position: relative;
  }
  .card {
    position: absolute;
    top: 236px;
    width: 540px;
    height: 308px;
    border-radius: 3px;
    overflow: hidden;
  }
  .card-front { left: 40px; background: var(--navy); color: var(--white); }
  .card-back { left: 620px; background: var(--orange); }

  .brand {
    position: absolute;
    left: 34px;
    top: 62px;
    width: 214px;
    display: flex;
    align-items: center;
    gap: 9px;
  }
  .brand-dot {
    width: 16px; height: 16px;
    flex: none;
    border-radius: 50%;
    background: var(--orange);
  }
  .brand-name {
    font-weight: 600;
    font-size: 18px;
    letter-spacing: 0.3px;
    color: var(--white);
    white-space: nowrap;
  }
  .divider {
    position: absolute;
    left: 268px;
    top: 58px;
    width: 2px;
    height: 180px;
    background: var(--orange);
  }
  .credential {
    position: absolute;
    left: 70px;
    bottom: 24px;
    font-size: 14px;
    font-weight: 400;
    color: var(--white);
    white-space: nowrap;
  }
  .contact-block {
    position: absolute;
    left: 292px;
    top: 100px;
  }
  .person-name {
    font-weight: 800;
    font-size: 28px;
    line-height: 1;
    white-space: nowrap;
  }
  .person-name .first { color: var(--orange); }
  .person-name .last { color: var(--white); }
  .person-role {
    font-size: 13px;
    font-weight: 600;
    margin-top: 4px;
    margin-bottom: 14px;
  }
  .contact-list { list-style: none; }
  .contact-item {
    display: flex;
    align-items: center;
    gap: 8px;
    font-size: 13px;
    font-weight: 600;
    margin-bottom: 6px;
    white-space: nowrap;
  }
  .contact-icon { width: 14px; height: 14px; flex: none; }

  .back-brand {
    position: absolute;
    inset: 0;
    display: flex;
    align-items: center;
    justify-content: center;
    gap: 14px;
  }
  .back-brand-name {
    font-weight: 600;
    font-size: 36px;
    letter-spacing: 1px;
    color: var(--orange-deep);
    white-space: nowrap;
  }
  .back-brand-dot {
    width: 26px; height: 26px;
    border-radius: 50%;
    background: var(--orange-deep);
  }
</style>
</head>
<body>
  <section class="card card-front">
    <div class="brand">
      <span class="brand-dot"></span>
      <span class="brand-name">Skylark Reelworks</span>
    </div>
    <div class="divider"></div>
    <p class="credential">NRD Certified Remote Pilot Fully Insured</p>
    <div class="contact-block">
      <p class="person-name"><span class="first">Owen</span> <span class="last">Tarrick</span></p>
      <p class="person-role">Owner</p>
      <ul class="contact-list">
        <li class="contact-item">
          <svg class="contact-icon" viewBox="0 0 16 16" aria-hidden="true"><path fill="#e58650" d="M3.5 1.5l2.5 0 1 3.5-1.6 1.2a8 8 0 0 0 4.4 4.4L11 9l3.5 1v2.5c0 1-1 2-2 2C6.5 14.5 1.5 9.5 1.5 3.5c0-1 1-2 2-2z"/></svg>
          614-502-7738
        </li>
        <li class="contact-item">
          <svg class="contact-icon" viewBox="0 0 16 16" aria-hidden="true"><g fill="none" stroke="#e58650" stroke-width="1.5"><circle cx="8" cy="8" r="6.5"/><ellipse cx="8" cy="8" rx="2.8" ry="6.5"/><path d="M1.5 8h13"/></g></svg>
          www.skylarkreelworks.example
        </li>
        <li class="contact-item">
          <svg class="contact-icon" viewBox="0 0 16 16" aria-hidden="true"><rect x="1" y="3" width="14" height="10" rx="1.5" fill="#e58650"/><path d="M1.5 4l6.5 5 6.5-5" fill="none" stroke="#161a47" stroke-width="1.3"/></svg>
          info@skylarkreelworks.example
        </li>
      </ul>
    </div>
  </section>

  <section class="card card-back">
    <div class="back-brand">
      <span class="back-brand-dot"></span>
      <span class="back-brand-name">Skylark Reelworks</span>
    </div>
  </section>
</body>
</html>
```